Automotive eCommerce Business looking for a business card design

Looking for a clean and simple business card design. Our company name is "Brindle Auto" and we are a company specializing in the ecommerce sales of automotive parts, specifically for pick up trucks and large SUVs. Our company colours are red, black, and white.

Feel free to use the logo provided or create a new logo that you seem fit. Looking forward to your creative ideas!

Industry/Entity Type

Automotive

Contact Information for Business Card

We were thinking of a possibly two-sided design featuring just the logo and company name on one side, and personal information on the other side. Single sided designs will be considered as well.

Font styles to use
Serif
Sans Serif
Decorative

Colors
ec1f27
ffffff
000000

Requirements
Must have
• Space for employee's name, title, phone number and email address, along with the company address and website somewhere.

```html
<!DOCTYPE html>
<html lang="en">
<head>
<meta charset="utf-8">
<title>Brindle Auto Ltd — Business Card</title>
<link rel="stylesheet" href="https://fonts.googleapis.com/css2?family=Open+Sans:wght@400;600&display=swap">
<style>
  :root {
    --backdrop: #3b3532;
    --card: #0d0d0d;
    --card-edge: #1c1c1c;
    --brand-red: #c8262c;
    --text-white: #f2f2f2;
    --silver: #c9c9c9;
    --divider: #2e2e2e;
  }
  * { box-sizing: border-box; margin: 0; padding: 0; }
  html, body {
    width: 1200px; height: 900px; overflow: hidden;
    background: var(--backdrop);
    font-family: "Open Sans", Arial, sans-serif;
  }
  .stage {
    position: relative; width: 1200px; height: 900px;
    display: flex; align-items: center; justify-content: center; gap: 50px;
  }
  .card {
    width: 530px; height: 310px;
    background: var(--card);
    border: 1px solid var(--card-edge);
    box-shadow: 0 10px 30px rgba(0,0,0,.45);
    position: relative;
  }
  /* Back: personal details */
  .card-back { display: flex; }
  .brand-panel {
    width: 44%;
    margin: 40px 0; height: calc(100% - 80px);
    display: flex; flex-direction: column; align-items: center; justify-content: center; gap: 16px;
    border-right: 1px solid var(--divider);
  }
  .brand-mark { width: 70px; height: 70px; background: var(--brand-red); }
  .brand-name-red {
    color: var(--brand-red); font-weight: 600; font-size: 22px; letter-spacing: .3px;
  }
  .details { padding: 56px 0 0 34px; color: var(--text-white); }
  .person-name { color: var(--brand-red); font-size: 21px; font-weight: 400; line-height: 1.1; }
  .person-title { font-size: 14px; margin-top: 3px; }
  .address { font-size: 14px; line-height: 1.4; margin-top: 20px; }
  .contact-list { list-style: none; margin-top: 18px; font-size: 14px; line-height: 1.55; }
  .contact-list li { display: flex; align-items: center; gap: 10px; }
  .contact-list svg { width: 12px; height: 12px; fill: var(--brand-red); flex: none; }
  /* Front: brand only */
  .card-front {
    display: flex; flex-direction: column; align-items: center; justify-content: center; gap: 26px;
  }
  .front-mark { width: 78px; height: 78px; background: var(--silver); }
  .brand-name-silver {
    color: var(--silver); font-weight: 600; font-size: 28px; letter-spacing: .3px;
  }
</style>
</head>
<body>
<main class="stage">
  <section class="card card-back" aria-label="Business card back, personal details">
    <div class="brand-panel">
      <div class="brand-mark"></div>
      <span class="brand-name-red">Brindle Auto</span>
    </div>
    <div class="details">
      <h1 class="person-name">Marcus Hale</h1>
      <p class="person-title">Managing Director</p>
      <p class="address">4820 Harlow Road, Unit 7<br>Dunmore Vale, 204815.</p>
      <ul class="contact-list">
        <li><svg viewBox="0 0 24 24" aria-hidden="true"><path d="M6.6 10.8a15 15 0 0 0 6.6 6.6l2.2-2.2c.3-.3.7-.4 1-.2 1.1.4 2.3.6 3.6.6.6 0 1 .4 1 1V20c0 .6-.4 1-1 1A17 17 0 0 1 3 4c0-.6.4-1 1-1h3.5c.6 0 1 .4 1 1 0 1.300.2 2.500.6 3.600.1.3 0 .7-.2 1z"/></svg>044-555 010 234</li>
        <li><svg viewBox="0 0 24 24" aria-hidden="true"><path d="M2 5h20v14H2zm2 2v.5l8 5 8-5V7l-8 5z"/></svg>info@brindleauto.com</li>
        <li><svg viewBox="0 0 24 24" aria-hidden="true"><path d="M10.6 13.4a1 1 0 0 1 0-1.4l3-3a1 1 0 1 1 1.4 1.4l-3 3a1 1 0 0 1-1.4 0zM8.5 20a4.5 4.5 0 0 1-3.2-7.7l2.5-2.5 1.4 1.4-2.5 2.5a2.5 2.5 0 0 0 3.6 3.6l2.5-2.5 1.4 1.4-2.5 2.5A4.5 4.5 0 0 1 8.5 20zm7.7-5.8-1.4-1.4 2.5-2.5a2.5 2.5 0 0 0-3.6-3.6l-2.5 2.5-1.4-1.4 2.5-2.5a4.5 4.5 0 0 1 6.4 6.4z"/></svg>www.brindleauto.com</li>
      </ul>
    </div>
  </section>

  <section class="card card-front" aria-label="Business card front, company name">
    <div class="front-mark"></div>
    <span class="brand-name-silver">Brindle Auto Ltd</span>
  </section>
</main>
</body>
</html>
```